Tolbek cards

I want a simple business card that pops.
Logo on one side.
On side two i want.
"Are you thinking about a new building on your property, or renovating an existing structure? Contact".....
Owners Name: Dale Whitacre
Owners Phone number: 610-555-0187
Address:4076 Copper Ridge RD, Harlow Falls, OH 43917
Committed to Quality, Service, and Integrity

```html
<!DOCTYPE html>
<html lang="en">
<head>
<meta charset="utf-8">
<title>Tolbek Builders – Business Cards</title>
<link rel="stylesheet" href="https://fonts.googleapis.com/css2?family=Arimo:ital,wght@0,400;0,700;1,400;1,700&display=swap">
<style>
  :root {
    --backdrop: #5a5a5a;
    --card: #ffffff;
    --brown-dark: #3f2c1b;
    --ink-brown: #4a321f;
    --ink-grey: #545454;
    --white: #ffffff;
  }
  html, body {
    margin: 0;
    padding: 0;
    width: 1200px;
    height: 1200px;
    overflow: hidden;
    background: var(--backdrop);
    font-family: "Arimo", Arial, sans-serif;
  }
  .canvas { position: relative; width: 1200px; height: 1200px; }
  .card {
    position: absolute;
    left: 260px;
    width: 690px;
    height: 394px;
    background: var(--card);
    overflow: hidden;
  }
  .card--contact { top: 158px; }
  .card--brand { top: 652px; }
  .card__shapes { position: absolute; inset: 0; width: 100%; height: 100%; }
  .shape-dark { fill: var(--brown-dark); }

  .pitch {
    position: absolute;
    left: 26px;
    top: 48px;
    margin: 0;
    white-space: nowrap;
    font-size: 18.5px;
    line-height: 24px;
    letter-spacing: 0.5px;
    font-style: italic;
    font-weight: 700;
    color: var(--ink-brown);
  }
  .owner-name {
    position: absolute;
    left: 24px;
    top: 224px;
    margin: 0;
    white-space: nowrap;
    font-size: 29px;
    font-weight: 700;
    letter-spacing: 0.3px;
    color: var(--brown-dark);
  }
  .owner-phone {
    position: absolute;
    left: 26px;
    top: 280px;
    margin: 0;
    display: flex;
    align-items: center;
    gap: 5px;
    font-size: 16px;
    color: var(--ink-grey);
  }
  .owner-phone svg { width: 14px; height: 14px; fill: var(--brown-dark); }
  .owner-address {
    position: absolute;
    left: 26px;
    top: 316px;
    margin: 0;
    white-space: nowrap;
    font-size: 16px;
    line-height: 21px;
    font-style: normal;
    color: var(--ink-grey);
  }
  .values {
    position: absolute;
    left: 390px;
    top: 261px;
    width: 170px;
    margin: 0;
    text-align: center;
    white-space: nowrap;
    font-size: 18px;
    line-height: 24px;
    font-style: italic;
    color: var(--white);
  }
  .mark-name { position: absolute; margin: 0; font-weight: 700; }
  .card--contact .mark-name {
    left: 505px;
    top: 92px;
    width: 160px;
    text-align: center;
    font-size: 34px;
    color: var(--white);
  }
  .card--brand .mark-name {
    left: 80px;
    top: 140px;
    width: 480px;
    text-align: center;
    font-size: 72px;
    color: var(--brown-dark);
  }
</style>
</head>
<body>
<main class="canvas">

  <section class="card card--contact" aria-label="Business card, contact side">
    <svg class="card__shapes" viewBox="0 0 690 394" preserveAspectRatio="none" aria-hidden="true">
      <defs>
        <radialGradient id="lightBrown" cx="0.6" cy="0.35" r="0.8">
          <stop offset="0" stop-color="#9c8569"/>
          <stop offset="1" stop-color="#7c6048"/>
        </radialGradient>
      </defs>
      <polygon class="shape-dark" points="311,0 690,0 690,394"/>
      <polygon points="477,173 263,394 690,394" fill="url(#lightBrown)"/>
    </svg>

    <p class="pitch">Are you thinking about a<br>new building on your property,<br>or renovating an existing<br>structure?</p>
    <h2 class="owner-name">DALE WHITACRE</h2>
    <p class="owner-phone">
      <svg viewBox="0 0 24 24" aria-hidden="true"><path d="M6.6 10.8a15.1 15.1 0 0 0 6.6 6.6l2.2-2.2a1 1 0 0 1 1-.25 11.4 11.4 0 0 0 3.6.57 1 1 0 0 1 1 1V20a1 1 0 0 1-1 1A17 17 0 0 1 3 4a1 1 0 0 1 1-1h3.5a1 1 0 0 1 1 1c0 1.25.2 2.45.57 3.57a1 1 0 0 1-.25 1z"/></svg>
      610-555-0187
    </p>
    <address class="owner-address">4076 Copper Ridge RD<br>Harlow Falls, OH 43917</address>
    <p class="values">Committed to<br>Quality,<br>Service and<br>Integrity</p>
    <p class="mark-name">Tolbek</p>
  </section>

  <section class="card card--brand" aria-label="Business card, brand side">
    <svg class="card__shapes" viewBox="0 0 690 394" preserveAspectRatio="none" aria-hidden="true">
      <defs>
        <linearGradient id="lightBrownCorner" x1="1" y1="0.5" x2="0.7" y2="1">
          <stop offset="0" stop-color="#9a8268"/>
          <stop offset="1" stop-color="#7a5c44"/>
        </linearGradient>
      </defs>
      <polygon class="shape-dark" points="503,0 690,0 690,194"/>
      <polygon points="690,201 690,394 503,394" fill="url(#lightBrownCorner)"/>
    </svg>
    <h1 class="mark-name">Tolbek</h1>
  </section>

</main>
</body>
</html>
```